I need a business card designed using the logo provided either vertical or horizontal......Harbourline Property Group is an Australian based real estate company that caters for the upper end of the market so the design of the business card "must reflect" the companies image!!
Colour combinations are optional but "must be realistic" and must be able to be accurately useable CMYK colours.
Please consider that any colours used "must be able to be used" and be suitable in following designs for "pull out banner signs" and "real estate signs".
The colours and the font in the attached designs are for example and other combinations are encouraged.
Target Market(s)
The High End of the Australian real estate market
Industry/Entity Type
Business
Contact Information for Business Card
Logo - Business Name - Director + Licensed Real Estate Agent - Mobile Number (Cell Phone) - Business Number - Fax - Email Address - Web address
Requirements
Must have
- Designs and colours (CMYK) that can easily be interpreted by an Australian printer.
Nice to have
- Some alternative ideas on colour and font..........the ones provided are ok and have been provided as an example but I am looking for alternative ideas
Should not have
- Loud, overly bright colours. Designs that do not reflect the professional standards of the business.
- Designs that look good on a computer monitor but can not be re-created on a printing press.............this is most important when it comes to shading etc.

```html
<!DOCTYPE html>
<html lang="en">
<head>
<meta charset="utf-8">
<title>Harbourline Property Group — Business Card</title>
<link rel="stylesheet" href="https://fonts.googleapis.com/css2?family=PT+Sans:wght@400;700&display=swap">
<style>
  :root {
    --backdrop: #2a2a2a;
    --card-white: #f7f7f5;
    --gold: #a9781f;
    --gold-deep: #8a6219;
    --gold-light: #d2c08e;
    --ink: #1e1e1e;
    --cream: #efe2c4;
    --brown: #4a3208;
  }
  * { margin: 0; padding: 0; box-sizing: border-box; }
  html, body {
    width: 1200px; height: 873px; overflow: hidden;
    background: var(--backdrop);
    font-family: "PT Sans", Arial, sans-serif;
  }
  .stage {
    position: relative; width: 1200px; height: 873px;
    display: flex; align-items: center; justify-content: center;
  }
  .business-card {
    position: relative; width: 840px; height: 480px;
    background: var(--card-white);
    overflow: hidden;
    box-shadow: 0 12px 30px rgba(0,0,0,0.45);
  }
  .card-swoosh { position: absolute; inset: 0; width: 100%; height: 100%; }
  .brand {
    position: absolute; left: 300px; top: 92px;
    display: flex; align-items: center; gap: 14px;
  }
  .brand-mark { width: 22px; height: 22px; background: var(--gold); }
  .brand-name {
    font-weight: 700; font-size: 30px; letter-spacing: 1px;
    color: var(--ink); text-transform: uppercase;
  }
  .holder { position: absolute; left: 54px; top: 360px; }
  .holder-name { font-size: 30px; color: var(--cream); letter-spacing: 0.5px; }
  .holder-title { font-size: 19px; color: var(--brown); margin-top: 4px; }
  .contact-list {
    position: absolute; left: 520px; top: 218px; list-style: none;
  }
  .contact-item {
    display: flex; align-items: center; gap: 12px;
    font-size: 18px; color: var(--ink); height: 32px;
  }
  .contact-icon { width: 18px; height: 18px; fill: var(--cream); stroke: var(--cream); }
</style>
</head>
<body>
<main class="stage">
  <article class="business-card">
    <svg class="card-swoosh" viewBox="0 0 840 480" preserveAspectRatio="none" aria-hidden="true">
      <defs>
        <linearGradient id="gold-fill" x1="0" y1="0" x2="0" y2="1">
          <stop offset="0" stop-color="#b1801f"/>
          <stop offset="1" stop-color="#8c6318"/>
        </linearGradient>
      </defs>
      <path d="M0 296 C 250 186, 560 126, 840 136 L840 480 L0 480 Z" fill="var(--gold-light)"/>
      <path d="M0 310 C 250 200, 560 140, 840 150 L840 480 L0 480 Z" fill="url(#gold-fill)"/>
    </svg>

    <div class="brand">
      <span class="brand-mark"></span>
      <span class="brand-name">Harbourline Property Group</span>
    </div>

    <div class="holder">
      <p class="holder-name">Daniel Ashford</p>
      <p class="holder-title">Chief Operating Officer</p>
    </div>

    <ul class="contact-list">
      <li class="contact-item">
        <svg class="contact-icon" viewBox="0 0 20 20" aria-label="Phone" role="img"><path stroke="none" d="M3 6c0-2 2-3 7-3s7 1 7 3v2h-4V6.5H7V8H3z M5 9h10l2 8H3z"/></svg>
        <span>412-555-0148</span>
      </li>
      <li class="contact-item">
        <svg class="contact-icon" viewBox="0 0 20 20" aria-label="Fax" role="img"><path stroke="none" d="M6 2h8v5H6z M2 8h16v7h-3v3H5v-3H2z M7 13v3h6v-3z"/></svg>
        <span>412-555-0149</span>
      </li>
      <li class="contact-item">
        <svg class="contact-icon" viewBox="0 0 20 20" aria-label="Email" role="img"><path stroke="none" d="M2 4h16v12H2z"/><path fill="none" stroke="var(--gold)" stroke-width="1.5" d="M2 4l8 7 8-7"/></svg>
        <span>dan@harbourlinegroup.com</span>
      </li>
      <li class="contact-item">
        <svg class="contact-icon" viewBox="0 0 20 20" aria-label="Website" role="img"><g fill="none" stroke-width="2.2"><rect x="3" y="9" width="7" height="9" rx="3.5" transform="rotate(-45 6.5 13.5)"/><rect x="10" y="2" width="7" height="9" rx="3.5" transform="rotate(-45 13.5 6.5)"/></g></svg>
        <span>www.harbourlinegroup.com</span>
      </li>
    </ul>
  </article>
</main>
</body>
</html>
```